Whitcombe Business Card Design

The name of the business is Dario Whitcombe, CPA LLC
The service that we offer is Accounting, Tax & Consulting Services. I need it to have the following items:
Dario Whitcombe, Principal
Phone Number
Email Address
Physical Address

I have attached the company logo, one in black and one in white. Please provide a design in black background and the other in white background. Please include "Accounting, Tax & Consulting Services". I want the business card to be clean and very professional.

```html
<!DOCTYPE html>
<html lang="en">
<head>
<meta charset="utf-8">
<title>Dario Whitcombe, CPA LLC – Business Card</title>
<link href="https://fonts.googleapis.com/css2?family=Montserrat:wght@500;600;700&family=Roboto:wght@300;400&display=swap" rel="stylesheet">
<style>
  :root {
    --backdrop: #2c2c2c;
    --card: #ececec;
    --ink: #3a3a3c;
    --grey: #7b7b7d;
    --bar-grey: #8e8e90;
    --red: #8e1518;
    --body: #3d3d3d;
  }
  * { margin: 0; padding: 0; box-sizing: border-box; }
  html, body { width: 1200px; height: 1138px; overflow: hidden; }
  body { background: var(--backdrop); position: relative; font-family: "Roboto", Arial, sans-serif; }

  .card {
    position: absolute;
    background: var(--card);
    border-radius: 14px;
    overflow: hidden;
  }
  .card--front { left: 272px; top: 184px; width: 622px; height: 376px; }
  .card--back  { left: 274px; top: 606px; width: 619px; height: 375px; }

  .brand-square { position: absolute; background: var(--ink); }
  .card--front .brand-square { left: 266px; top: 96px; width: 91px; height: 91px; }
  .card--back .brand-square { left: 57px; top: 108px; width: 166px; height: 166px; }

  .wordmark {
    font-family: "Montserrat", Arial, sans-serif;
    font-weight: 600;
    color: var(--ink);
    white-space: nowrap;
    letter-spacing: 0.2px;
  }
  .subtitle {
    font-family: "Montserrat", Arial, sans-serif;
    font-weight: 600;
    color: var(--grey);
    white-space: nowrap;
    letter-spacing: 2px;
  }

  .card--front .wordmark { position: absolute; top: 200px; width: 100%; text-align: center; font-size: 25px; }
  .card--front .subtitle { position: absolute; top: 233px; width: 100%; text-align: center; font-size: 18px; }
  .tagline {
    position: absolute; top: 328px; width: 100%; text-align: center;
    font-size: 16px; color: #222;
  }
  .accent-bar { position: absolute; left: 0; bottom: 0; width: 100%; height: 9px; display: flex; }
  .accent-bar span:first-child { flex: 1; background: var(--red); }
  .accent-bar span:last-child { flex: 1; background: var(--bar-grey); }

  .details { position: absolute; left: 282px; right: 34px; top: 54px; }
  .details .wordmark { font-size: 18.5px; letter-spacing: 0; }
  .details .subtitle { font-size: 14px; letter-spacing: 1.5px; margin-top: 3px; }
  .person-name {
    font-family: "Montserrat", Arial, sans-serif; font-weight: 700;
    color: var(--red); font-size: 20px; letter-spacing: 0.6px; margin-top: 28px;
  }
  .person-role { font-size: 16px; font-weight: 300; color: var(--body); margin-top: 1px; }
  .address { font-size: 16px; font-weight: 300; color: var(--body); line-height: 24px; margin-top: 29px; }
  .contact-list { list-style: none; margin-top: 4px; }
  .contact-list li {
    display: flex; align-items: center; height: 24px;
    font-size: 16px; font-weight: 300; color: var(--body);
  }
  .contact-list svg { width: 14px; height: 14px; margin-right: 12px; fill: var(--red); }
</style>
</head>
<body>

<section class="card card--front">
  <div class="brand-square"></div>
  <div class="wordmark">DARIO WHITCOMBE, CPA, LLC</div>
  <div class="subtitle">CERTIFIED PUBLIC ACCOUNTANT</div>
  <p class="tagline">Accounting, Tax &amp; Consulting Services</p>
  <div class="accent-bar"><span></span><span></span></div>
</section>

<section class="card card--back">
  <div class="brand-square"></div>
  <div class="details">
    <div class="wordmark">DARIO WHITCOMBE, CPA, LLC</div>
    <div class="subtitle">CERTIFIED PUBLIC ACCOUNTANT</div>
    <div class="person-name">DARIO WHITCOMBE</div>
    <div class="person-role">Principal</div>
    <p class="address">1234, Anywhere Street, Any City,<br>Any Town Name, US 123456</p>
    <ul class="contact-list">
      <li>
        <svg viewBox="0 0 16 16" aria-hidden="true"><path d="M1 6c0-2 3-3 7-3s7 1 7 3v1h-3V5.5C11 5 9.5 5 8 5s-3 0-4 .5V7H1z"/><path d="M4 8h8l1.5 6h-11z"/></svg>
        828-555-0142
      </li>
      <li>
        <svg viewBox="0 0 16 16" aria-hidden="true"><path d="M1 3h14v10H1z M2.5 4.5 8 9l5.5-4.5v7h-11z" fill-rule="evenodd"/></svg>
        dw@dariowhitcombellc.com
      </li>
      <li>
        <svg viewBox="0 0 16 16" aria-hidden="true"><circle cx="8" cy="8" r="7"/><path d="M1 8h14M8 1v14M3 4h10M3 12h10" stroke="#ececec" stroke-width="1" fill="none"/></svg>
        www.dariowhitcombellc.com
      </li>
    </ul>
  </div>
</section>

</body>
</html>
```